Communication and Marketing agency needs a new presentation card

We are a group of communication and marketing agencies specialized in companies that are in the logistics and industrial sector. The head agency is TELVANO Grupo and the group consists of 4 agencies: TELVANO Media, TELVANO Digital, TELVANO Research and DifundeEnPantalla. We hace 4 offices in Spain (Madrid, Barcelona, Valencia and Murcia). We are looking for a clean and attractive design that transmits our experience, brand presence in the market and knowledge to those who receive the card.It has to maintain the colors of the logo that is attached.
Target Market(s)
logistics and industrial sector
Marketing department
Contact Information for Business Card
Clean and attractive design

```html
<!DOCTYPE html>
<html lang="en">
<head>
<meta charset="utf-8">
<title>TELVANO Grupo – Business Card</title>
<link rel="stylesheet" href="https://fonts.googleapis.com/css2?family=Montserrat:wght@400;700&display=swap">
<style>
  :root {
    --bg: #4a4b4e;
    --card: #ffffff;
    --red: #c8202f;
    --grey: #555658;
    --text: #6b6c6f;
  }
  * { margin: 0; padding: 0; box-sizing: border-box; }
  html, body { width: 1200px; height: 960px; overflow: hidden; }
  body {
    background: var(--bg);
    font-family: "Montserrat", sans-serif;
    position: relative;
  }
  .card {
    position: absolute;
    left: 250px;
    width: 700px;
    height: 400px;
    background: var(--card);
    box-shadow: 0 10px 30px rgba(0,0,0,.35);
  }
  .card--logos { top: 60px; }
  .card--contact { top: 500px; }

  /* logo card */
  .brand-grid {
    position: absolute;
    left: 0; right: 0; top: 125px;
    display: grid;
    grid-template-columns: max-content max-content;
    justify-content: center;
    row-gap: 56px;
    column-gap: 56px;
  }
  .brand-name {
    font-weight: 700;
    font-size: 24px;
    letter-spacing: .3px;
    white-space: nowrap;
  }
  .brand-name--red { color: var(--red); }
  .brand-name--grey { color: var(--grey); }

  /* contact card */
  .head-brand {
    position: absolute;
    right: 70px; top: 70px;
    font-weight: 700;
    font-size: 40px;
    color: var(--red);
    letter-spacing: 1px;
    white-space: nowrap;
  }
  .divider {
    position: absolute;
    left: 60px; top: 230px;
    width: 590px; height: 3px;
    display: flex;
  }
  .divider__grey { flex: 0 0 52%; background: var(--grey); }
  .divider__red { flex: 1; background: var(--red); }

  .person { position: absolute; left: 60px; top: 158px; }
  .person__name { font-weight: 700; font-size: 28px; line-height: 36px; color: var(--red); }
  .person__title { font-size: 20px; line-height: 26px; color: var(--text); }

  .contacts {
    position: absolute;
    left: 60px; top: 250px;
    list-style: none;
  }
  .contacts li {
    display: flex; align-items: center;
    font-size: 20px; color: var(--text);
    height: 34px;
    white-space: nowrap;
  }
  .contacts svg { width: 22px; height: 22px; margin-right: 16px; fill: var(--red); flex: none; }

  .address {
    position: absolute;
    left: 420px; top: 252px;
    display: flex; align-items: flex-start;
    font-size: 18px; line-height: 26px; color: var(--text);
    white-space: nowrap;
  }
  .address svg { width: 22px; height: 28px; margin-right: 14px; margin-top: 6px; fill: var(--red); flex: none; }
</style>
</head>
<body>

<section class="card card--logos" aria-label="Group agencies">
  <div class="brand-grid">
    <span class="brand-name brand-name--red">TELVANO Media</span>
    <span class="brand-name brand-name--grey">TELVANO Digital</span>
    <span class="brand-name brand-name--grey">TELVANO Research</span>
    <span class="brand-name brand-name--red">DifundeEnPantalla</span>
  </div>
</section>

<section class="card card--contact" aria-label="Contact details">
  <div class="head-brand">TELVANO Grupo</div>

  <div class="person">
    <div class="person__name">Your Name</div>
    <div class="person__title">Your Title</div>
  </div>

  <div class="divider"><span class="divider__grey"></span><span class="divider__red"></span></div>

  <ul class="contacts">
    <li>
      <svg viewBox="0 0 24 24" aria-hidden="true"><path d="M6.6 10.8a15.1 15.1 0 0 0 6.6 6.6l2.2-2.2a1 1 0 0 1 1-.25 11.4 11.4 0 0 0 3.6.57 1 1 0 0 1 1 1V20a1 1 0 0 1-1 1A17 17 0 0 1 3 4a1 1 0 0 1 1-1h3.5a1 1 0 0 1 1 1c0 1.25.2 2.450.57 3.57a1 1 0 0 1-.25 1z"/></svg>
      123-456-2100
    </li>
    <li>
      <svg viewBox="0 0 24 24" aria-hidden="true"><path d="M2 5h20v2l-10 6L2 7zM2 9l10 6 10-6v10H2z"/></svg>
      youremail@telvano.es
    </li>
    <li>
      <svg viewBox="0 0 24 24" aria-hidden="true"><path d="M12 2a10 10 0 1 0 0 20 10 10 0 0 0 0-20zm0 2c.9 1 1.7 2.6 2 4h-4c.3-1.4 1.1-3 2-4zM4.3 14a8 8 0 0 1 0-4h3.3a16 16 0 0 0 0 4zm.8 2h2.8c.3 1.3.8 2.5 1.4 3.4A8 8 0 0 1 5.1 16zm2.8-8H5.1a8 8 0 0 1 4.2-3.4C8.7 5.5 8.2 6.7 7.9 8zM12 20c-.9-1-1.7-2.6-2-4h4c-.3 1.4-1.1 3-2 4zm2.4-6H9.6a14 14 0 0 1 0-4h4.8a14 14 0 0 1 0 4zm.3 5.4c.6-.9 1.1-2.1 1.4-3.4h2.8a8 8 0 0 1-4.2 3.4zM16.4 14a16 16 0 0 0 0-4h3.3a8 8 0 0 1 0 4zm-.3-6c-.3-1.3-.8-2.5-1.4-3.4A8 8 0 0 1 18.9 8z"/></svg>
      www.yourwebsite.com
    </li>
  </ul>

  <div class="address">
    <svg viewBox="0 0 24 30" aria-hidden="true"><path d="M12 0a10 10 0 0 0-10 10c0 7.5 10 20 10 20s10-12.5 10-20A10 10 0 0 0 12 0zm0 14a4 4 0 1 1 0-8 4 4 0 0 1 0 8z"/></svg>
    <div>Your address, city<br>state, ZIP 0000</div>
  </div>
</section>

</body>
</html>
```